House Cleaning Platform for Consumers and Cleaners

UPDATE: I've attached screenshots showing a purchase flow example, something all designers have missed in their designs. PLEASE check the URLs I've included in the brief for examples of a cleaning website. I've seen mostly landing pages and nothing else.

WHAT I'M LOOKING FOR:
I need the UI designed for a house cleaning web platform from 2 separate experiences: one from the consumer end to order a cleaner to come clean their house and one from a cleaner’s end that manages their orders and manages their schedule.

The UI will need to include photo uploading for before and after photos, a checkout/cart experience w/ tips, toggle options for adding and removing rooms/extras cleaning add-ons, customer+cleaner reviews (meaning the cleaner finished the job and they can rate and review the customer as well as the customer can rate and review the cleaner), order history for consumers, job history for cleaners, profile, settings, and landing pages for both.

PLEASE DO NOT USE THE COLOR BLUE AS THE PRIMARY COLOR. Use a light green (HEX #2fdf86) instead for primary theming color.

REFERENCES:
If you'd like a few websites I've enjoyed for references, checkout:
larkpolish.example, vomby.example, and brightfernhome.example.

For sake of branding, the company name is PlumNest. Currently do not have a logo as we have not decided on the name. Logo will come later.

Feel free to reach out to me if you have any questions!
Updates

Most designer submissions were a landing page and only a landing page. Very few designed the flows I requested and none designed a schedule management page. I even updated the Brief to more clearly outline the needs and references. Only about 2-3 of the designers actually did more than a landing page. Still don't believe I received 6 designers input that I had paid for.

Target Market(s)

FULL-TIME WORKING HOUSEHOLDS, SINGLE PROFESSIONALS, SINGLE PARENTS, ELDERLY & MOBILITY CHALLENGED, BUSY BODIES.

Industry/Entity Type

Cleaning, gig work.

Number of Pages Required

5+ page

Font styles to use
Other font styles liked:
• Jost or Lexend are great Google Font options I've used in the pitch deck and horribly done app mockups.

Colors
00AB8E
00BBA5
67D7C9
C6EFE9
E9F9F6
59FF00
82FF00
B8FF75
E3FFCB
F4FFEA
FFF300
FFF600
FEFA6F
FFFEC7
FFFEE8
FFC000
F8CF3A
FAE287
FDF2CF
FEFAEE

Requirements
Must have
• Landing page, consumer flow, cleaner schedule management, checkout flow, Rate & Review for consumer and/or cleaner, order history, profile.
Nice to have
• I'd like it to be simple in design and modern, but not so simple it's boring. Iconography can sometimes break that up, but I don't want it looking busy. It's a cleaning platform so the UI should look clean.

```html
<!DOCTYPE html>
<html lang="en">
<head>
<meta charset="utf-8">
<title>PlumNest – Book Your Services</title>
<link href="https://fonts.googleapis.com/css2?family=Nunito:ital,wght@0,400;0,600;0,700;1,400&family=Open+Sans:wght@700&display=swap" rel="stylesheet">
<style>
:root{
  --green:#2bd283;
  --ink:#111418;
  --text:#2a2d31;
  --muted:#c4c6c9;
  --border:#d2d4d7;
  --white:#ffffff;
}
*{box-sizing:border-box;margin:0;padding:0}
html,body{width:1200px;height:974px;overflow:hidden;background:var(--white)}
body{position:relative;font-family:"Nunito",sans-serif;color:var(--ink)}
.abs{position:absolute}
.brand{left:101px;top:16px;font-family:"Open Sans",sans-serif;font-weight:700;font-size:31px;color:var(--green);line-height:1}
.nav a{position:absolute;top:27px;font-size:11.5px;font-weight:600;color:var(--ink);text-decoration:none;line-height:16px}
.search{left:731px;top:22.5px;width:218px;height:25px;border:1px solid var(--border);border-radius:13px;display:flex;align-items:center;padding-left:8px;gap:13px;font-size:11.5px;font-weight:600}
.login{left:981px;top:27px;font-size:11.5px;font-weight:600;line-height:16px}
.signup{left:1024px;top:22.5px;width:75px;height:25px;border-radius:13px;background:var(--green);font-size:10.5px;font-weight:600;display:flex;align-items:center;justify-content:center}
.page-title{left:0;width:1200px;top:126px;text-align:center;font-family:"Open Sans",sans-serif;font-weight:700;font-size:36px;line-height:50px}
.divider{left:0;top:214.5px;width:1200px;height:1px;background:var(--green)}
.section-title{left:101px;font-size:20px;font-weight:600;line-height:26px}
.optional{font-size:11.5px;color:var(--muted);font-weight:600;margin-left:10px}
.section-desc{left:101px;font-size:11.2px;color:var(--text);line-height:16px}
.option{width:468px;height:37px;border:1px solid var(--border);border-radius:2px;display:flex;align-items:center;padding:0 18px 0 18px;font-size:12px;font-weight:700}
.option .label{margin-left:14px;flex:1}
.radio{width:12px;height:12px;border-radius:50%;border:1px solid var(--border);flex:none}
.radio.on{border:3px solid var(--green)}
.link{font-size:11.5px;color:var(--muted);font-weight:400}
.agree{left:101px;top:706px;display:flex;align-items:center;gap:13px;font-size:12px;font-style:italic}
.btn{top:786px;width:175px;height:50px;border-radius:25px;display:flex;align-items:center;justify-content:center;font-size:15.5px;font-weight:600}
.btn.back{left:101px;border:1px solid var(--border)}
.btn.next{left:307.5px;background:var(--green)}
</style>
</head>
<body>
<div class="abs brand">PlumNest</div>
<nav class="nav">
  <a style="left:438px">Home</a>
  <a style="left:489px">Pricing</a>
  <a style="left:546px">Services</a>
  <a style="left:612px">Contact</a>
  <a style="left:674px">Help</a>
</nav>
<div class="abs search">
  <svg width="13" height="13" viewBox="0 0 14 14" fill="none" stroke="#111418" stroke-width="1.2"><circle cx="6" cy="6" r="5"/><path d="M9.7 9.7 13 13"/></svg>
  <span>Search</span>
</div>
<div class="abs login">Login</div>
<div class="abs signup">Sign Up</div>

<h1 class="abs page-title">Book Your Services Now</h1>
<div class="abs divider"></div>

<h2 class="abs section-title" style="top:281px">Type Of Cleaning</h2>
<p class="abs section-desc" style="top:321px">View and compare cleaning checklists below. Please review the excluded services list as soon as not covered</p>
<div class="abs option" style="left:101px;top:357.5px"><span class="radio on"></span><span class="label">Deep Cleaning</span><span class="link">View Checklist</span></div>
<div class="abs option" style="left:630px;top:357.5px"><span class="radio"></span><span class="label">Move In/Out Cleaning</span><span class="link">View Checklist</span></div>

<h2 class="abs section-title" style="top:447px">Add-On Services<span class="optional">(Optional)</span></h2>
<p class="abs section-desc" style="top:488px">These services can be included in addition to the cleaning checklist</p>

<div class="abs option" style="left:101px;top:524.5px"><span class="radio"></span><span class="label">Inside Fridge</span><svg class="help" width="13" height="13" viewBox="0 0 14 14" fill="none" stroke="#c4c6c9"><circle cx="7" cy="7" r="6"/><path d="M5.3 5.4a1.8 1.8 0 1 1 2.4 1.7c-.5.2-.7.6-.7 1.1"/><circle cx="7" cy="10.3" r=".4" fill="#c4c6c9"/></svg></div>
<div class="abs option" style="left:630px;top:524.5px"><span class="radio"></span><span class="label">Inside Cabinets</span><svg width="13" height="13" viewBox="0 0 14 14" fill="none" stroke="#c4c6c9"><circle cx="7" cy="7" r="6"/><path d="M5.3 5.4a1.8 1.8 0 1 1 2.4 1.7c-.5.2-.7.6-.7 1.1"/><circle cx="7" cy="10.3" r=".4" fill="#c4c6c9"/></svg></div>
<div class="abs option" style="left:101px;top:580.5px"><span class="radio"></span><span class="label">Wipe Baseboard</span><svg width="13" height="13" viewBox="0 0 14 14" fill="none" stroke="#c4c6c9"><circle cx="7" cy="7" r="6"/><path d="M5.3 5.4a1.8 1.8 0 1 1 2.4 1.7c-.5.2-.7.6-.7 1.1"/><circle cx="7" cy="10.3" r=".4" fill="#c4c6c9"/></svg></div>
<div class="abs option" style="left:630px;top:580.5px"><span class="radio"></span><span class="label">Inside Oven</span></div>
<div class="abs option" style="left:101px;top:636.5px"><span class="radio"></span><span class="label">Interior Windows</span><svg width="13" height="13" viewBox="0 0 14 14" fill="none" stroke="#c4c6c9"><circle cx="7" cy="7" r="6"/><path d="M5.3 5.4a1.8 1.8 0 1 1 2.4 1.7c-.5.2-.7.6-.7 1.1"/><circle cx="7" cy="10.3" r=".4" fill="#c4c6c9"/></svg></div>
<div class="abs option" style="left:630px;top:636.5px"><span class="radio"></span><span class="label">Wet Wipe Blinds</span><svg width="13" height="13" viewBox="0 0 14 14" fill="none" stroke="#c4c6c9"><circle cx="7" cy="7" r="6"/><path d="M5.3 5.4a1.8 1.8 0 1 1 2.4 1.7c-.5.2-.7.6-.7 1.1"/><circle cx="7" cy="10.3" r=".4" fill="#c4c6c9"/></svg></div>

<div class="abs agree"><span class="radio on"></span><span>I’ve read all the Checklists carefully</span></div>

<div class="abs btn back">Back</div>
<div class="abs btn next">Save &amp; Next</div>
</body>
</html>
```